Calm Summit website development

Need a website designed for a coaching business. Very high-end, luxury, professionalism, in the area of STRESS, see brief attached. I have a logo already
Updates

Slow in providing feedback

Target Market(s)

CEOs very successful men and wealthy females, high end luxury market

Industry/Entity Type

coaching

Number of Pages Required

1 page

Requirements
Must have
• Luxury look, professional, serious but warm, appealing to both sexes

```html
<!DOCTYPE html>
<html lang="en">
<head>
<meta charset="utf-8">
<title>Calm Summit – Lifestyle Coaching</title>
<link rel="stylesheet" href="https://fonts.googleapis.com/css2?family=Oswald:wght@500;600&family=Lato:wght@400;700&display=swap">
<style>
:root{
  --blue:#2f9be6;
  --blue-deep:#1d7fcb;
  --ink:#111111;
  --text:#333333;
  --muted:#9a9a9a;
  --light:#f4f4f4;
  --white:#ffffff;
  --black:#000000;
  --star:#f0a81c;
}
*{margin:0;padding:0;box-sizing:border-box}
html,body{width:1200px;height:3185px;overflow:hidden;background:var(--white)}
body{font-family:'Lato',sans-serif;color:var(--text);position:relative}
.page{position:relative;width:1200px;height:3185px;overflow:hidden}
.abs{position:absolute}
.head{font-family:'Oswald',sans-serif;font-weight:600;color:var(--ink)}
.btn{position:absolute;display:flex;align-items:center;justify-content:center;border-radius:30px;background:var(--blue);color:var(--white);font-family:'Oswald',sans-serif;font-weight:500;font-size:18px;text-decoration:none}

/* hero */
.hero{position:absolute;left:0;top:0;width:1200px;height:620px;background:linear-gradient(90deg,#0c0f13 0%,#1c232b 40%,#56606a 62%,#8b949c 80%,#4b5660 100%)}
.brand{position:absolute;left:112px;top:50px;display:flex;align-items:center;gap:10px;color:var(--white);font-family:'Oswald',sans-serif;font-weight:500;font-size:18px;letter-spacing:3px}
.brand .mark{width:14px;height:14px;background:var(--white)}
.nav{position:absolute;top:26px;left:604px;display:flex;gap:41px;font-size:15.5px;font-weight:700;color:var(--white)}
.nav .on{color:var(--blue)}
.hero h1{position:absolute;left:109px;top:200px;font-size:66px;color:var(--white);font-family:'Oswald',sans-serif;font-weight:500;line-height:1}
.hero p{position:absolute;left:109px;top:284px;width:470px;font-size:15px;line-height:26px;color:var(--white)}

/* why me */
.why{position:absolute;left:0;top:620px;width:1200px;height:381px;background:var(--light);text-align:center}
.why h2{position:absolute;left:0;right:0;top:75px;font-size:36px}
.why p{position:absolute;left:175px;width:850px;top:141px;font-size:15px;line-height:26px;color:var(--ink)}

/* benefits */
.benefits h2{position:absolute;left:0;right:0;top:1060px;text-align:center;font-size:42px}
.card{position:absolute;top:1164px;width:312px;height:426px}
.card .photo{position:absolute;inset:0}
.card .box{position:absolute;left:16px;top:207px;width:280px;height:199px;background:var(--white);text-align:center;padding-top:22px}
.card .box.tint{background:rgba(47,155,230,.82)}
.card h3{font-size:27px;font-weight:500}
.card p{font-size:14.5px;line-height:26px;color:var(--ink);margin:8px 20px 0}
.card .more{display:inline-block;margin-top:4px;font-family:'Oswald',sans-serif;font-weight:500;font-size:15px;color:var(--blue)}
.tint h3,.tint p,.tint .more{color:var(--white)}
.arrow{position:absolute;top:1368px}

/* welcome */
.welcome{position:absolute;left:0;top:1730px;width:1200px;height:405px;background:linear-gradient(90deg,#2b8fd9 0%,#3ea4ea 45%,#3f97d6 75%,#2d86cc 100%)}
.hex{position:absolute;left:111px;top:1662px}
.welcome h2{position:absolute;left:602px;top:30px;font-family:'Oswald',sans-serif;font-weight:500;font-size:40px;color:var(--white)}
.welcome p{position:absolute;left:605px;top:91px;width:480px;font-size:15px;line-height:25.8px;color:#e8f3fc}

/* testimonials */
.reviews h2{position:absolute;left:0;right:0;top:2280px;text-align:center;font-size:42px}
.quote{position:absolute;left:557px;top:2349px;width:57px;height:57px;border-radius:50%;background:var(--blue);display:flex;align-items:center;justify-content:center;color:var(--white);font-family:'Oswald',sans-serif;font-size:40px;line-height:1;padding-top:14px}
.stars{position:absolute;left:540px;top:2421px;display:flex;gap:3px}
.slide{position:absolute;text-align:center}
.slide .name{font-family:'Oswald',sans-serif;font-weight:500;font-size:19px;color:var(--ink)}
.slide p{margin-top:21px;font-size:15px;line-height:30px;color:var(--ink)}
.slide.side{opacity:.45}
.thanks{position:absolute;left:0;right:0;top:2608px;text-align:center;font-size:17px;font-weight:700;color:var(--ink)}
.date{position:absolute;left:0;right:0;top:2645px;text-align:center;font-size:15px;color:var(--ink)}
.track{position:absolute;left:267px;top:2704px;width:634px;height:4px;background:#d9d9d9}
.track span{position:absolute;left:227px;top:0;width:180px;height:4px;background:var(--blue)}

/* footer */
.footer{position:absolute;left:0;top:2782px;width:1200px;height:403px;background:var(--black);color:var(--white)}
.col{position:absolute;top:56px}
.col h4{font-family:'Oswald',sans-serif;font-weight:500;font-size:18px}
.col h4::after{content:"";display:block;width:30px;height:2px;background:var(--blue);margin-top:8px}
.col ul{list-style:none;margin-top:18px;font-size:15px}
.col li{display:flex;align-items:flex-start;gap:10px;margin-bottom:12px;line-height:26px}
.ico{flex:none;margin-top:7px}
.field{width:243px;border-bottom:1px solid #555;padding:8px 0 12px;font-size:15px;color:#bdbdbd;margin-bottom:14px}
.submit{position:relative;width:139px;height:40px;margin-top:20px;box-shadow:0 4px 18px rgba(47,155,230,.6)}
.rule{position:absolute;left:112px;top:312px;width:976px;height:1px;background:#222}
.copy{position:absolute;left:0;right:0;top:344px;text-align:center;font-size:15px}
</style>
</head>
<body>
<div class="page">

  <header class="hero">
    <div role="img" aria-label="Photo of a smiling woman holding a coffee mug and a phone in an office" class="abs" style="left:560px;top:0;width:640px;height:620px;background:linear-gradient(160deg,rgba(110,120,128,.4),rgba(200,200,198,.35) 55%,rgba(60,70,80,.3))"></div>
    <div class="brand"><span class="mark"></span>CALM SUMMIT</div>
    <nav class="nav"><span class="on">Home</span><span>About</span><span>Benefits</span><span>Our Blog</span><span>Contact Us</span></nav>
    <h1>Head Coach Get it</h1>
    <p>Lorem ipsum dolor sit amet, consectetur adipiscing elit, sed do ei-usmod tempor incididunt ut labore et dolore magna aliqua.</p>
    <a class="btn" style="left:110px;top:365px;width:147px;height:55px">Get Started</a>
  </header>

  <section class="why">
    <h2 class="head">Why Me</h2>
    <p>Been there done that! Have been through a lot, started businesses, selling a business, law suits, marriage, divorce, second marriage, kids, school, sports, fights, robbed, gun in face, traveled the world, successful, two great kids Limited number of clients...different stage of life, empty nester, have a full career...won't be a number</p>
    <a class="btn" style="left:528px;top:251px;width:147px;height:56px">Learn More</a>
  </section>

  <section class="benefits">
    <h2 class="head">Our Benefits</h2>
    <svg class="arrow" style="left:44px" width="16" height="18" viewBox="0 0 16 18"><path d="M11 2 4 9l7 7" fill="none" stroke="#111" stroke-width="2"/></svg>
    <svg class="arrow" style="left:1134px" width="16" height="18" viewBox="0 0 16 18"><path d="M5 2l7 7-7 7" fill="none" stroke="#111" stroke-width="2"/></svg>

    <article class="card" style="left:111px">
      <div class="photo" role="img" aria-label="Photo of stacked smooth stones on raked sand" style="background:linear-gradient(180deg,#6f8aa6 0%,#3e5570 40%,#8aa0b6 100%)"></div>
      <div class="box"><h3 class="head">Experience</h3><p>Lorem ipsum dolor sit amet, con-sectetur adipiscing elit, sed do ei-usmod tempor</p><span class="more">Learn More »</span></div>
    </article>
    <article class="card" style="left:444px">
      <div class="photo" role="img" aria-label="Photo of a woman meditating in front of misty mountains" style="background:linear-gradient(180deg,#9fc0d8 0%,#7a9fb9 45%,#4e6b7f 100%)"></div>
      <div class="box tint"><h3 class="head">Health/Wellness</h3><p>Sector expert Health/Wellness. Presented at numerous industry shows and quoted in national ...</p><span class="more">Learn More »</span></div>
    </article>
    <article class="card" style="left:776px">
      <div class="photo" role="img" aria-label="Photo of a hiker raising arms under a cloudy sky" style="background:linear-gradient(180deg,#b9cdd6 0%,#dfe7ea 40%,#8f9a8c 100%)"></div>
      <div class="box"><h3 class="head">Excellent listener</h3><p>Excellent listener...being in sales for many years, the secret is to really listen...</p><span class="more">Learn More »</span></div>
    </article>
  </section>

  <section class="welcome">
    <h2>Welcome to CalmSummit</h2>
    <p>Calm Summit came about due to my desire to help people lead a better and healthier life. Initially, I was involved in the fitness/body side of health. As years passed and my experience grew, I realized how important the mind was in total wellness, and that the mind is all powerful and controlling. Control the mind, control the body and achieve success. Stress can be the most debilating factor in our lives, it is the root cause of so many diseases and costs the US workplace an estimated 300 billion dollars due to loss of productivity.</p>
    <a class="btn" style="left:606px;top:314px;width:132px;height:51px;background:var(--white);color:var(--blue)">Learn More</a>
  </section>
  <svg class="hex" width="454" height="550" viewBox="0 0 454 550" role="img" aria-label="Photo of a woman doing a yoga pose on a lakeside dock at sunset">
    <defs>
      <linearGradient id="hexFill" x1="0" y1="0" x2="0" y2="1">
        <stop offset="0" stop-color="#cfe0e6"/>
        <stop offset=".55" stop-color="#b7c6c4"/>
        <stop offset="1" stop-color="#c98c48"/>
      </linearGradient>
    </defs>
    <polygon points="227,0 454,120 454,430 227,550 0,430 0,120" fill="url(#hexFill)"/>
  </svg>

  <section class="reviews">
    <h2 class="head">Client Testimonials</h2>
    <div class="quote">“</div>
    <div class="stars">
      <svg width="82" height="14" viewBox="0 0 82 14" fill="var(--star)">
        <g id="st"><path d="M7 0l2 4.6 5 .4-3.8 3.2 1.2 4.9L7 10.5 2.6 13.1l1.2-4.9L0 5l5-.4z"/></g>
        <use href="#st" x="17"/><use href="#st" x="34"/><use href="#st" x="51"/><use href="#st" x="68"/>
      </svg>
    </div>
    <div class="slide" style="left:258px;top:2453px;width:654px">
      <div class="name">Morgan Ellery</div>
      <p>Lorem ipsum dolor sit amet, consectetur adipiscing elit, sed do eiusmod tempor incididunt ut labore et dolore magna aliqua. Quis ipsum suspendisse ultrices gravida. Risus commodo viver-ra maecenas accumsan Lorem ipsum dolor sit amet, consectetur</p>
    </div>
    <div class="slide side" style="left:-462px;top:2453px;width:654px;text-align:right">
      <div class="name">Morgan Ellery</div>
      <p>Lorem ipsum dolor sit amet, consectetur adipiscing elit, sed do eiusmod tempor incididunt ut labore et dolore magna aliqua. Quis ipsum suspendisse ultrices gravida. Risus commodo viver-ra maecenas accumsan Lorem ipsum dolor sit amet, consectetur</p>
    </div>
    <div class="slide side" style="left:978px;top:2453px;width:654px;text-align:left">
      <div class="name" style="padding-left:175px">Morgan Ellery</div>
      <p>Lorem ipsum dolor sit amet, consectetur adipiscing elit, sed do eiusmod tempor incididunt ut labore et dolore magna aliqua. Quis ipsum suspendisse ultrices gravida. Risus commodo viver-ra maecenas accumsan Lorem ipsum</p>
    </div>
    <div class="thanks">Thanks Calm Summit</div>
    <div class="date">Feb 12,2022</div>
    <div class="track"><span></span></div>
  </section>

  <footer class="footer">
    <div class="col" style="left:112px">
      <h4>Contact</h4>
      <ul>
        <li><svg class="ico" width="11" height="14" viewBox="0 0 11 14"><path d="M5.5 0A5.5 5.5 0 0 0 0 5.5C0 9.5 5.5 14 5.5 14S11 9.5 11 5.5A5.5 5.5 0 0 0 5.5 0zm0 7.5a2 2 0 1 1 0-4 2 2 0 0 1 0 4z" fill="var(--blue)"/></svg><span>Lorem ipsum dolor<br>sit amet</span></li>
        <li><svg class="ico" width="12" height="12" viewBox="0 0 12 12"><path d="M2.4 0 4.6 2.6 3.4 4.2a7 7 0 0 0 4.4 4.4L9.4 7.4 12 9.6 10.6 12C4.8 11.6.4 7.2 0 1.4z" fill="var(--blue)"/></svg><span>+1 555-014-2290</span></li>
        <li><svg class="ico" width="14" height="11" viewBox="0 0 14 11"><rect width="14" height="11" rx="1" fill="var(--blue)"/><path d="M1 1.5l6 4.5 6-4.5" fill="none" stroke="#000" stroke-width="1.2"/></svg><span>info@calmsummit.example</span></li>
      </ul>
    </div>
    <div class="col" style="left:367px">
      <h4>Help Link</h4>
      <ul>
        <li style="margin-bottom:4px"><span>›</span><span>Terms&amp;condtions</span></li>
        <li style="margin-bottom:4px"><span>›</span><span>Privacy Policy</span></li>
        <li style="margin-bottom:4px"><span>›</span><span>About Us</span></li>
        <li style="margin-bottom:4px"><span>›</span><span>Support</span></li>
      </ul>
    </div>
    <div class="col" style="left:629px;top:58px">
      <h4>Follow us</h4>
      <ul>
        <li style="margin-bottom:4px"><svg class="ico" width="11" height="11"><circle cx="5.5" cy="5.5" r="5" fill="#fff"/></svg><span>Community</span></li>
        <li style="margin-bottom:4px"><svg class="ico" width="11" height="11"><circle cx="5.5" cy="5.5" r="5" fill="#fff"/></svg><span>Gallery</span></li>
        <li style="margin-bottom:4px"><svg class="ico" width="11" height="11"><circle cx="5.5" cy="5.5" r="5" fill="#fff"/></svg><span>Updates</span></li>
        <li style="margin-bottom:4px"><svg class="ico" width="11" height="11"><circle cx="5.5" cy="5.5" r="5" fill="#fff"/></svg><span>Videos</span></li>
      </ul>
    </div>
    <div class="col" style="left:843px">
      <h4 style="margin-bottom:10px">Newsletter updates</h4>
      <div class="field">Name*</div>
      <div class="field">Email*</div>
      <a class="btn submit">Submit Now</a>
    </div>
    <div class="rule"></div>
    <div class="copy">© 2022 Calm Summit All Rights Reserved</div>
  </footer>

</div>
</body>
</html>
```